Business card for Crestline Bathrooms

Please design a business card for our bathroom renovation business. You can use my existing logo, but if you have an idea to modernize it, I would like to see it. Please see attached files first. I would like to use the blue and the orange theme. I like the concept of using the shower head in the logo. Please find following a design (or two) that I have been trying to create with my limited resources. That design was for a sign, but I was going to adopt it and use it as a business card as well. I like the concept of the water splash but I don’t think it “flows” nicely together with the logo. Another thought is that maybe creating the logo out of water splash could work and have a dramatic effect (like the water text and the butterfly picture attached with similar background instead of white). If the above doesn’t work I would like to see a modern simplified design. One of the attached files named as the unwanted business card has all the details that I want included in the business card. Please note that it is two sided.
Updates

I am very thankful for the designs that I have received, but they are very similar and only a couple of attempts to do something with the water splash as per my original brief. Modernizing the logo and having it made out of out of water splash with the orange as color accent could work and have a dramatic effect (like the water text and the butterfly picture attached with similar background instead of white). Please do not use the butterfly itself! This is just an example that images can be created out of water splash.

Contact Information for Business Card

all the details are on the unwonted business card file included

Colors
3176b5

Requirements
Nice to have
• Copied from the brief:
• ... maybe creating the logo out of water splash could work and have a dramatic effect (like the water text and the butterfly picture attached with similar background instead of white). Please do not use the butterfly itself!
Should not have
• I am getting designs with a butterfly. The butterfly picture was an example of creating something from a water splash. The butterfly itself has no association with anything other than the concept of creating a logo out of water splash. Sorry, I thought I was clear in the brief.

```html
<!DOCTYPE html>
<html lang="en">
<head>
<meta charset="utf-8">
<title>Crestline Bathrooms – Business Card</title>
<link rel="stylesheet" href="https://fonts.googleapis.com/css2?family=Roboto:wght@400;500;700&family=Roboto+Condensed:wght@700&display=swap">
<style>
  :root {
    --stage: #2a2a2c;
    --card: #202022;
    --brand-blue: #3176b5;
    --accent-orange: #e8907a;
    --text-light: #f4f4f4;
    --badge-grey: #6a6a6c;
    --divider: #8a8a8c;
  }
  * { box-sizing: border-box; margin: 0; padding: 0; }
  html, body {
    width: 1200px; height: 900px; overflow: hidden;
    background: var(--stage);
    font-family: "Roboto", Arial, sans-serif;
  }
  .stage {
    width: 1200px; height: 900px;
    display: flex; flex-direction: column; align-items: center; justify-content: center;
    gap: 32px;
  }
  .card {
    position: relative;
    width: 640px; height: 366px;
    background: var(--card);
    box-shadow: 0 10px 28px rgba(0,0,0,.45);
    color: var(--text-light);
  }

  /* Front side */
  .card-front {
    display: flex; flex-direction: column; align-items: center;
    padding-top: 58px;
  }
  .brand {
    display: flex; align-items: center; gap: 12px;
  }
  .brand-dot {
    width: 22px; height: 22px; border-radius: 50%;
    background: var(--accent-orange);
  }
  .brand-name {
    font-family: "Roboto", Arial, sans-serif;
    font-weight: 700; font-size: 34px; letter-spacing: .5px;
    color: var(--brand-blue);
  }
  .services {
    list-style: none; margin-top: 26px; text-align: center;
    font-size: 15.5px; font-weight: 500; line-height: 20px; letter-spacing: .3px;
  }
  .memberships {
    margin-top: 24px;
    display: flex; align-items: center; gap: 18px;
  }
  .membership-badge {
    width: 34px; height: 34px; border-radius: 4px;
    background: var(--badge-grey);
  }
  .membership-badge.wide { width: 96px; height: 30px; }
  .membership-divider {
    width: 1px; height: 34px; background: var(--divider);
  }

  /* Back side */
  .holder-name {
    position: absolute; left: 62px; top: 150px;
    font-family: "Roboto Condensed", "Arial Narrow", sans-serif;
    font-weight: 700; font-size: 30px; letter-spacing: .5px;
    color: var(--brand-blue);
  }
  .contact-divider {
    position: absolute; left: 318px; top: 104px;
    width: 1px; height: 132px;
    background: linear-gradient(var(--card), var(--divider) 30%, var(--divider) 70%, var(--card));
  }
  .contact-list {
    position: absolute; left: 338px; top: 112px;
    list-style: none; font-size: 17px; font-weight: 500; line-height: 24px;
  }
  .contact-list li { display: flex; align-items: center; gap: 10px; }
  .icon { width: 15px; height: 15px; fill: var(--brand-blue); flex: none; }
  .postal {
    position: absolute; left: 176px; top: 290px;
    display: flex; align-items: center; gap: 8px;
    font-size: 18px; font-weight: 500;
  }
  .postal .icon { width: 16px; height: 20px; }
</style>
</head>
<body>
<main class="stage">

  <section class="card card-front" aria-label="Business card front">
    <div class="brand">
      <span class="brand-dot"></span>
      <span class="brand-name">Crestline Bathrooms</span>
    </div>
    <ul class="services">
      <li>Complete Bathroom Renovations &amp; Remodelling</li>
      <li>Highly Skilled &amp; Qualified Tradespeople</li>
      <li>Professional Service From Concept To Completion</li>
      <li>All Work Guaranteed</li>
    </ul>
    <div class="memberships" aria-label="Industry memberships">
      <span class="membership-badge"></span>
      <span class="membership-divider"></span>
      <span class="membership-badge wide"></span>
    </div>
  </section>

  <section class="card card-back" aria-label="Business card back">
    <h1 class="holder-name">DANIEL MARSH</h1>
    <span class="contact-divider"></span>
    <ul class="contact-list">
      <li>
        <svg class="icon" viewBox="0 0 16 16"><path d="M3.6 1.2l2.3 2.4-1.2 1.8c.9 2 2.4 3.6 4.4 4.6l1.8-1.2 2.5 2.3-1.3 2.3C7 13.3 2.7 9 1.2 3z"/></svg>
        <span>0400 555 182</span>
      </li>
      <li>
        <svg class="icon" viewBox="0 0 16 16"><path d="M4.5 1h7a1 1 0 0 1 1 1v12a1 1 0 0 1-1 1h-7a1 1 0 0 1-1-1V2a1 1 0 0 1 1-1zm.5 2v9h6V3zm3 9.6a.8.8 0 1 0 0 1.6.8.8 0 0 0 0-1.6z"/></svg>
        <span>5550 1294</span>
      </li>
      <li>
        <svg class="icon" viewBox="0 0 16 16"><path d="M1 3h14v10H1zm1.5 1.3v.4L8 8.4l5.5-3.7v-.4z"/></svg>
        <span>daniel@crestlinebathrooms.com.au</span>
      </li>
      <li>
        <svg class="icon" viewBox="0 0 16 16"><path d="M8 1a7 7 0 1 0 0 14A7 7 0 0 0 8 1zm-1 2.2c-.6 1-1 2.3-1.1 3.8H3.1A5 5 0 0 1 7 3.2zM3.1 9h2.8c.1 1.5.5 2.8 1.1 3.8A5 5 0 0 1 3.1 9zm4.8 4c-.6-.9-1-2.3-1.1-4h2.4c-.1 1.7-.5 3.1-1.3 4zM6.8 7c.1-1.7.5-3.1 1.2-4 .7.9 1.1 2.3 1.2 4zm2.2 5.8c.6-1 1-2.3 1.1-3.8h2.8A5 5 0 0 1 9 12.8zM10.1 7C10 5.5 9.6 4.2 9 3.2A5 5 0 0 1 12.9 7z"/></svg>
        <span>crestlinebathrooms.com.au</span>
      </li>
    </ul>
    <p class="postal">
      <svg class="icon" viewBox="0 0 16 20"><path d="M8 0a7 7 0 0 0-7 7c0 5 7 13 7 13s7-8 7-13a7 7 0 0 0-7-7zm0 10a3 3 0 1 1 0-6 3 3 0 0 1 0 6z"/></svg>
      <span>PO Box 41, Harwood Vale 2690</span>
    </p>
  </section>

</main>
</body>
</html>
```